Moxy Fen needs some awesome stationary

Do you have what it takes to get my brand? You either do or you don't, have a crack at a design and you my just win my business.

I don't want to waste your or my time, so put your creative genius on either a business card or envelope.

I however need a package of stationary that follows the same brand. I will message you to complete the remaining should I like your first submission.

Here is what I need, have a go!

Basically I need the following for my small business based in melbourne.
- Letterhead (printer ready and MS Word)
- Business Card
- Compliments Slip
- Envelope
- Proposal Cover Page (MS Word only)
- Presentation Folder
- Marbled Fox Cards
- Student Name Tent
- Index Cards
- Vell-Ka

I am establishing the brand and it must be modern, professional but also relaxed; that is not formal and not corporate. It represents a company are leaders, but small enough to care and operate like a bunch of friends. We are bringing people and conversations back to business, and turfing out all the bureaucracy and crazy and wasteful procedures. Its about "lets talk and figure it out together and find even better ways".

Target Market(s)

Mainly companies that build software products, but Agile practices are used in many other industries (even graphic design projects)

Industry/Entity Type

Information Technology

Font styles to use
Sans Serif

Colors
3176b5
aaaaaa

Requirements
Must have
• I like curves and circles and not boxes or rectangles.
• I want a colour rich design with my brand colours, but it must be balanced.
• I want more modern than traditional, but simple modern
Should not have
• Not corporate
• Please don't waste my time if your not going to think about it.
• Don't mess with my primary logo
• Don't change my colours
• Don't overlay logo on image

```html
<!DOCTYPE html>
<html lang="en">
<head>
<meta charset="utf-8">
<title>Moxy Fen — Compliments Slip</title>
<link rel="stylesheet" href="https://fonts.googleapis.com/css2?family=Open+Sans:wght@400;600;700&family=Pinyon+Script&display=swap">
<style>
  :root {
    --brand-blue: #2c5ba3;
    --brand-grey: #939dae;
    --text-grey: #4f4f55;
    --rule: #7d8fae;
    --paper: #ffffff;
    --desk: #898a8e;
  }
  * { margin: 0; padding: 0; box-sizing: border-box; }
  html, body {
    width: 1200px;
    height: 694px;
    overflow: hidden;
  }
  body {
    background: var(--desk);
    font-family: "Open Sans", Arial, sans-serif;
    position: relative;
  }
  .compliments-slip {
    position: absolute;
    left: 92px;
    top: 105px;
    width: 998px;
    height: 477px;
    background: var(--paper);
    box-shadow: 0 1px 4px rgba(0, 0, 0, 0.35);
  }
  .brand {
    position: absolute;
    left: 52px;
    top: 50px;
    display: flex;
    flex-direction: column;
    align-items: flex-start;
    gap: 8px;
  }
  .brand-mark {
    width: 64px;
    height: 64px;
    display: block;
  }
  .brand-name {
    font-weight: 700;
    font-size: 25px;
    line-height: 1;
    color: var(--brand-blue);
    letter-spacing: -0.2px;
  }
  .greeting {
    position: absolute;
    right: 58px;
    top: 352px;
    font-family: "Pinyon Script", cursive;
    font-size: 56px;
    line-height: 1;
    color: var(--brand-blue);
    white-space: nowrap;
  }
  .contact {
    position: absolute;
    left: 52px;
    top: 396px;
    width: 887px;
    font-size: 13px;
    color: var(--text-grey);
  }
  .contact-address {
    line-height: 1;
    padding-bottom: 4px;
    border-bottom: 1px solid var(--rule);
  }
  .contact-lines {
    margin-top: 6px;
    line-height: 1;
  }
  .contact-label {
    font-weight: 700;
    color: var(--brand-blue);
  }
  .contact-web {
    font-weight: 700;
    color: var(--brand-blue);
    letter-spacing: 1.2px;
    text-decoration: none;
  }
</style>
</head>
<body>
  <main class="compliments-slip">
    <header class="brand">
      <svg class="brand-mark" viewBox="0 0 64 64" aria-hidden="true">
        <circle cx="32" cy="32" r="30" fill="var(--brand-blue)"/>
      </svg>
      <span class="brand-name">Moxy Fen</span>
    </header>

    <p class="greeting">With Compliments</p>

    <footer class="contact">
      <p class="contact-address">PO Box 4180, Ferncliff Vale, VIC 3190 , Australia</p>
      <p class="contact-lines">
        <span class="contact-label">P:</span> 13 000 MOXYF |
        <a class="contact-web" href="#">www.moxy-fen.com.au</a>
      </p>
    </footer>
  </main>
</body>
</html>
```